DELCOURT ROOFING YARD SIGN

We need a yard sign to put in our customers' yards when we are roofing their home.
Delcourt Roofing
417 Tobin Rd
Lake Charles LA 70615
phone: 337-555-0182

Maybe some verbiage like "Your Hometown Roofing Experts"
or
"Family Owned Since 1956"

```html
<!DOCTYPE html>
<html lang="en">
<head>
<meta charset="utf-8">
<title>Delcourt Roofing Yard Sign</title>
<link rel="stylesheet" href="https://fonts.googleapis.com/css2?family=Montserrat:wght@600;700;800;900&display=swap">
<style>
  :root {
    --page-bg: #7a7a7a;
    --band-black: #000000;
    --band-black-glow: #2b2b2b;
    --navy-deep: #13123a;
    --navy-bright: #10107a;
    --ink-navy: #14123e;
    --panel-white: #ffffff;
    --divider: #111111;
    --emblem-ring: #8a8a8a;
    --text-white: #ffffff;
  }
  * { margin: 0; padding: 0; box-sizing: border-box; }
  html, body {
    width: 1200px; height: 1200px; overflow: hidden;
    background: var(--page-bg);
    font-family: "Montserrat", sans-serif;
  }
  .yard-sign {
    position: absolute; left: 50px; top: 187px;
    width: 1100px; height: 825px; overflow: hidden;
    background: radial-gradient(ellipse 60% 70% at 50% 100%, var(--navy-bright), var(--navy-deep));
  }
  .top-band {
    position: absolute; left: 0; top: 0; width: 100%; height: 400px;
    background: radial-gradient(ellipse 50% 80% at 50% 20%, var(--band-black-glow), var(--band-black));
  }
  .headline {
    position: absolute; left: 0; top: 44px; width: 100%;
    text-align: center; color: var(--text-white);
    font-weight: 700; font-size: 87px; line-height: 81px;
    letter-spacing: 2px; white-space: nowrap;
  }
  .service-panel {
    position: absolute; left: 55px; top: 242px; width: 962px; height: 381px;
    background: var(--panel-white); border-radius: 24px;
  }
  .brand-mark {
    position: absolute; left: 40px; top: 50px; width: 364px; height: 280px;
    display: flex; flex-direction: column; align-items: center; justify-content: center; gap: 22px;
  }
  .brand-mark .brand-circle {
    width: 120px; height: 120px; border-radius: 50%;
    border: 6px solid var(--emblem-ring);
  }
  .brand-mark .brand-name {
    color: var(--ink-navy); font-weight: 800; font-size: 38px; line-height: 44px;
    text-align: center; letter-spacing: 1px;
  }
  .panel-divider {
    position: absolute; left: 476px; top: 33px; width: 5px; height: 308px;
    background: var(--divider);
  }
  .service-list {
    position: absolute; left: 516px; top: 0; list-style: none;
    color: var(--ink-navy); font-weight: 800; font-size: 74px; letter-spacing: -1px;
  }
  .service-list li { position: absolute; left: 0; white-space: nowrap; line-height: 1; }
  .service-list li:nth-child(1) { top: 37px; }
  .service-list li:nth-child(2) { top: 151px; }
  .service-list li:nth-child(3) { top: 266px; }
  .phone-line {
    position: absolute; left: 78px; top: 637px;
    display: flex; align-items: center; gap: 22px; color: var(--text-white);
  }
  .phone-line svg { width: 70px; height: 86px; }
  .phone-number {
    font-weight: 900; font-size: 121px; line-height: 1; letter-spacing: -2px; white-space: nowrap;
  }
  .address {
    position: absolute; left: 0; top: 766px; width: 100%;
    text-align: center; color: var(--text-white);
    font-weight: 600; font-size: 38px; letter-spacing: 0.5px; white-space: nowrap;
  }
</style>
</head>
<body>
  <div class="yard-sign">
    <div class="top-band"></div>
    <h1 class="headline">YOUR HOMETOWN<br>ROOFING EXPERTS</h1>

    <div class="service-panel">
      <div class="brand-mark">
        <div class="brand-circle"></div>
        <div class="brand-name">DELCOURT<br>ROOFING</div>
      </div>
      <div class="panel-divider"></div>
      <ul class="service-list">
        <li>ROOFING</li>
        <li>SIDING</li>
        <li>CHIMNEYS</li>
      </ul>
    </div>

    <div class="phone-line">
      <svg viewBox="0 0 70 86" aria-hidden="true">
        <path d="M10 6 L22 2 L30 22 L22 30 C24 42 32 54 40 60 L50 54 L62 70 L52 80 C30 82 6 50 4 22 Z"
              fill="none" stroke="#ffffff" stroke-width="6" stroke-linejoin="round"/>
        <path d="M38 24 A14 14 0 0 1 48 40" fill="none" stroke="#ffffff" stroke-width="4" stroke-linecap="round"/>
        <path d="M40 12 A26 26 0 0 1 58 42" fill="none" stroke="#ffffff" stroke-width="4" stroke-linecap="round"/>
        <path d="M42 1 A38 38 0 0 1 68 44" fill="none" stroke="#ffffff" stroke-width="4" stroke-linecap="round"/>
      </svg>
      <span class="phone-number">337-555-0182</span>
    </div>

    <p class="address">417 TOBIN RD LAKE CHARLES LA 70615</p>
  </div>
</body>
</html>
```